Quality Monitoring Company Needs a New Site

We are an established company that has a fair number of clients but the site lacks current design standards that we'd like to keep up with. We'd like to mimic the same style of the site on plinkora.com, vetrumo.com, https://brindlecoffer.com/, etc. We'd also like to make sure the designer understands SEO Silos and how it effects the design elements. Attached is the structure that I'd like to follow for the pages. You don't need to design every single sub-page because they'll probably be fairly similar; however, I want to see at least 1 each. Please use the content on our current site for filler areas. Please try to do a good job of understanding what we do so you can use your best judgement on what is needed to be successful. Use our color scheme and the logo should be the side view but I included the AI just in case.
Updates

I am narrowing down on the field of designs that I have received. There are a lot of similarities between the designs I like and don't like. I'd also like to ensure that some of the inner pages get done in the next 5 days so I can see the creativity that is there as well. That is probably what is next -- getting a few inner pages completed so I can see what you can come up with (not based on our current website) because the current "front pages" are all so good and so close.

Industry/Entity Type

Telecommunications

Colors

Designer to choose colors to be used in the design.

Requirements
Must have
• SEO Silo Look and Feel
• Current Colors
Should not have
• No stockphotos whatsoever. NONE.

```html
<!DOCTYPE html>
<html lang="en">
<head>
<meta charset="utf-8">
<title>VoxMetric – Quality Assurance</title>
<link href="https://fonts.googleapis.com/css2?family=Montserrat:wght@400;500;600;700;800&display=swap" rel="stylesheet">
<style>
:root{
  --page:#f5f7fb;
  --navy:#0e2b5c;
  --navy-dark:#0b2550;
  --blue:#1a9fe0;
  --cyan:#0bb3ec;
  --text:#4a5466;
  --ring:#e2eefb;
  --panel:#e7eef2;
  --white:#ffffff;
}
*{box-sizing:border-box;margin:0;padding:0}
html,body{width:1200px;height:3527px;overflow:hidden}
body{position:relative;background:var(--page);font-family:'Montserrat',sans-serif;color:var(--text)}
.abs{position:absolute}
.ring{position:absolute;border-radius:50%;border:58px solid var(--ring)}
.ring-soft{position:absolute;border-radius:50%;background:#eaf2fc}

/* header */
.brand{left:138px;top:58px;display:flex;align-items:center;gap:8px;font-size:22px;font-weight:600;color:var(--navy)}
.brand .dot{width:16px;height:16px;border-radius:50%;background:var(--blue)}
.nav{left:404px;top:78px;display:flex;font-size:12.5px;font-weight:500;color:#2a3348}
.nav span{position:absolute;white-space:nowrap}
.nav .active{color:var(--blue);font-weight:700}
.dropdown{left:443px;top:107px;width:182px;height:128px;background:var(--white);box-shadow:0 4px 18px rgba(20,50,100,.08)}
.dropdown .item{position:absolute;left:17px;font-size:12px;color:#4a5466}
.dropdown .current{left:7px;top:4px;width:170px;height:26px;background:var(--cyan);color:#fff;font-weight:600;padding:7px 10px;font-size:11.5px}
.phone{left:903px;top:63px;display:flex;align-items:center;gap:11px;font-weight:700;font-size:14.5px;color:var(--navy)}
.phone .ico{width:38px;height:38px;border-radius:50%;background:var(--blue);display:flex;align-items:center;justify-content:center}

/* hero */
.hero-title{left:138px;top:190px;font-size:30px;font-weight:800;color:var(--navy)}
.hero-title em{font-style:normal;font-weight:500;color:var(--blue)}
.hero-rule{left:140px;top:238px;width:36px;height:2px;background:var(--blue)}
.copy{font-size:12.3px;line-height:19px;color:var(--text)}
.checks{list-style:none}
.checks li{position:absolute;left:0;white-space:nowrap;font-size:12.3px;padding-left:23px}
.checks li svg{position:absolute;left:0;top:3px}
.hero-art{left:595px;top:157px;width:513px;height:431px;border-radius:24px;background:radial-gradient(circle at 55% 45%,#dfe9f8 0%,#eef3fb 60%,rgba(245,247,251,0) 75%)}

/* feature sections */
.feature{position:absolute;left:0;width:1200px;height:487px}
.feature h2{position:absolute;font-size:21px;font-weight:700;color:var(--navy)}
.feature .copy{position:absolute;width:400px}
.feature .checks{position:absolute;width:420px;height:130px}

/* dashboard mock */
.dash{position:absolute;width:384px;height:283px;background:var(--panel);box-shadow:0 14px 30px rgba(20,50,100,.12);overflow:hidden}
.dash .bar{position:absolute;left:0;top:0;width:100%;height:16px;background:var(--navy)}
.dash .card{position:absolute;background:var(--white)}
.dash .profile{left:11px;top:30px;width:105px;height:120px}
.dash .avatar{position:absolute;left:25px;top:12px;width:56px;height:56px;border-radius:50%;background:var(--cyan)}
.dash .handle{position:absolute;left:0;top:76px;width:100%;text-align:center;font-size:6px;color:#555}
.dash .line{position:absolute;height:2px;background:#d3dae2;border-radius:1px}
.dash .feed{left:138px;top:30px;width:107px;height:253px}
.dash .feed .hero{position:absolute;left:0;top:0;width:100%;height:73px;background:linear-gradient(160deg,#16b2ea,#0b8fd0)}
.dash .feed .foot{position:absolute;left:0;bottom:0;width:100%;height:36px;background:var(--cyan)}
.dash .contacts{left:268px;top:30px;width:105px;height:133px}
.dash .calendar{left:268px;top:174px;width:105px;height:88px}
.dash .label{position:absolute;left:5px;top:4px;font-size:6px;color:#555}
.dash .pip{position:absolute;width:8px;height:8px;border-radius:50%}

/* footer */
.footer{left:0;top:3256px;width:1200px;height:271px;background:var(--navy-dark)}
.footer h3{position:absolute;font-size:16.5px;font-weight:700;color:var(--cyan)}
.footer .link{position:absolute;font-size:11.5px;color:#fff}
.footer .info{position:absolute;font-size:12.5px;color:#fff;line-height:23px}
.footer .mark{position:absolute;left:930px;top:60px;display:flex;align-items:center;gap:10px;font-size:24px;font-weight:600;color:#fff}
.footer .mark .dot{width:22px;height:22px;border-radius:50%;background:var(--cyan)}
.footer .rule{position:absolute;left:138px;top:220px;width:920px;height:1px;background:rgba(255,255,255,.18)}
.footer .copyright{position:absolute;left:0;top:238px;width:100%;text-align:center;font-size:12.5px;color:#fff}
</style>
</head>
<body>

<!-- decorative rings -->
<div class="ring-soft" style="left:760px;top:-140px;width:560px;height:560px"></div>
<div class="ring" style="left:800px;top:-100px;width:480px;height:480px;border-color:#e4eefb"></div>

<!-- header -->
<div class="abs brand"><span class="dot"></span>VoxMetric</div>
<nav class="abs nav">
  <span style="left:0">Home</span>
  <span class="active" style="left:58px">Services</span>
  <span style="left:132px">Industries</span>
  <span style="left:216px">Pricing</span>
  <span style="left:279px">Team</span>
  <span style="left:337px">Blog</span>
  <span style="left:388px">Contact Us</span>
</nav>
<div class="abs dropdown">
  <div class="item current">Quality Assurance</div>
  <div class="item" style="top:44px">Coaching</div>
  <div class="item" style="top:72px">Sales Performance</div>
  <div class="item" style="top:101px">AI Enabled Voice Analytics</div>
</div>
<div class="abs phone">
  <span class="ico"><svg width="16" height="16" viewBox="0 0 24 24" fill="#fff"><path d="M6.6 10.8a15.1 15.1 0 0 0 6.6 6.6l2.2-2.2c.3-.3.7-.4 1-.2 1.1.4 2.3.6 3.6.6.6 0 1 .4 1 1V20c0 .6-.4 1-1 1A17 17 0 0 1 3 4c0-.6.4-1 1-1h3.5c.6 0 1 .4 1 1 0 1.3.2 2.5.6 3.6.1.3 0 .7-.2 1z"/></svg></span>
  800-555-0142
</div>

<!-- hero -->
<h1 class="abs hero-title">Quality <em>Assurance</em></h1>
<div class="abs hero-rule"></div>
<p class="abs copy" style="left:142px;top:261px;width:460px">Lorem ipsum dolor sit amet, consectetuer adipiscing elit, sed diam nonummy nibh euismod tincidunt ut laoreet dolore magna aliquam erat volutpat. Ut wisi enim ad minim veniam, quis nostrud exerci tation ullamcorper suscipit lobortis nisl ut aliquip ex ea commodo consequat.</p>
<p class="abs copy" style="left:142px;top:356px;width:460px">Lorem ipsum dolor sit amet, consectetuer adipiscing elit, sed diam nonummy nibh euismod tincidunt ut laoreet dolore magna aliquam erat volutpat. Ut wisi enim ad minim veniam, quis nostrud exerci tation</p>
<ul class="abs checks" style="left:142px;top:433px;width:460px;height:130px">
  <li style="top:0"><svg width="10" height="8" viewBox="0 0 10 8"><path d="M1 4l3 3 5-6" stroke="#1a9fe0" stroke-width="2" fill="none"/></svg>Consectetuer adipiscing elit sed diam nonummy</li>
  <li style="top:32px"><svg width="10" height="8" viewBox="0 0 10 8"><path d="M1 4l3 3 5-6" stroke="#1a9fe0" stroke-width="2" fill="none"/></svg>Nibh euismod tincidunt ut laoreet dolore magna</li>
  <li style="top:65px"><svg width="10" height="8" viewBox="0 0 10 8"><path d="M1 4l3 3 5-6" stroke="#1a9fe0" stroke-width="2" fill="none"/></svg>Aliquam erat volutpat. Ut wisi enim ad minim veniam</li>
  <li style="top:98px"><svg width="10" height="8" viewBox="0 0 10 8"><path d="M1 4l3 3 5-6" stroke="#1a9fe0" stroke-width="2" fill="none"/></svg>Quis nostrud exerci tation ullamcorper suscipit lobortis</li>
</ul>
<div class="abs hero-art" role="img" aria-label="Illustration of a team reviewing a quality checklist dashboard with check marks around it"></div>

<!-- feature sections: mock left / text right alternating -->
<section class="feature" style="top:788px">
  <div class="ring" style="left:-30px;top:-128px;width:480px;height:480px"></div>
  <div class="dash" style="left:176px;top:0">
    <div class="bar"></div>
    <div class="card profile"><div class="avatar"></div><div class="handle">@username</div><div class="line" style="left:12px;top:90px;width:81px"></div><div class="line" style="left:18px;top:96px;width:69px"></div><div class="line" style="left:22px;top:106px;width:60px"></div></div>
    <div class="card feed"><div class="hero"></div><div class="line" style="left:6px;top:88px;width:90px"></div><div class="line" style="left:6px;top:95px;width:80px"></div><div class="line" style="left:6px;top:102px;width:86px"></div><div class="line" style="left:6px;top:140px;width:90px"></div><div class="line" style="left:6px;top:147px;width:78px"></div><div class="line" style="left:6px;top:180px;width:88px"></div><div class="line" style="left:6px;top:187px;width:72px"></div><div class="foot"></div></div>
    <div class="card contacts"><div class="label">Contact</div><div class="pip" style="left:6px;top:20px;background:#f29b42"></div><div class="pip" style="left:6px;top:44px;background:#9b5cc6"></div><div class="pip" style="left:6px;top:68px;background:#6b86c9"></div><div class="pip" style="left:6px;top:92px;background:#e0645a"></div><div class="pip" style="left:6px;top:116px;background:#8cc4a8"></div></div>
    <div class="card calendar"><div class="label">Calendar</div><div class="line" style="left:8px;top:22px;width:88px"></div><div class="line" style="left:8px;top:38px;width:88px"></div><div class="line" style="left:8px;top:48px;width:88px"></div><div class="line" style="left:8px;top:58px;width:88px"></div><div class="line" style="left:8px;top:68px;width:88px"></div><div class="line" style="left:8px;top:78px;width:20px"></div></div>
  </div>
  <h2 style="left:648px;top:18px">Cotetuer Adipiscing</h2>
  <p class="copy" style="left:649px;top:68px;width:400px">Lorem ipsum dolor sit amet, consectetuer adipiscing elit, sed diam nonummy nibh euismod tincidunt ut laoreet dolore magna aliquam erat volutpat. Ut wisi enim ad minim veniam</p>
  <ul class="checks" style="left:649px;top:146px">
    <li style="top:0"><svg width="10" height="8" viewBox="0 0 10 8"><path d="M1 4l3 3 5-6" stroke="#1a9fe0" stroke-width="2" fill="none"/></svg>Consectetuer adipiscing elit sed diam nonummy</li>
    <li style="top:32px"><svg width="10" height="8" viewBox="0 0 10 8"><path d="M1 4l3 3 5-6" stroke="#1a9fe0" stroke-width="2" fill="none"/></svg>Nibh euismod tincidunt ut laoreet dolore magna</li>
    <li style="top:64px"><svg width="10" height="8" viewBox="0 0 10 8"><path d="M1 4l3 3 5-6" stroke="#1a9fe0" stroke-width="2" fill="none"/></svg>Aliquam erat volutpat. Ut wisi enim ad minim veniam</li>
    <li style="top:96px"><svg width="10" height="8" viewBox="0 0 10 8"><path d="M1 4l3 3 5-6" stroke="#1a9fe0" stroke-width="2" fill="none"/></svg>Quis nostrud exerci tation ullamcorper suscipit lobortis</li>
  </ul>
</section>

<section class="feature" style="top:1275px">
  <div class="ring" style="left:740px;top:-100px;width:480px;height:480px"></div>
  <h2 style="left:137px;top:18px">Client Calibration</h2>
  <p class="copy" style="left:138px;top:68px;width:400px">Lorem ipsum dolor sit amet, consectetuer adipiscing elit, sed diam nonummy nibh euismod tincidunt ut laoreet dolore magna aliquam erat volutpat. Ut wisi enim ad minim veniam</p>
  <ul class="checks" style="left:138px;top:146px">
    <li style="top:0"><svg width="10" height="8" viewBox="0 0 10 8"><path d="M1 4l3 3 5-6" stroke="#1a9fe0" stroke-width="2" fill="none"/></svg>Consectetuer adipiscing elit sed diam nonummy</li>
    <li style="top:32px"><svg width="10" height="8" viewBox="0 0 10 8"><path d="M1 4l3 3 5-6" stroke="#1a9fe0" stroke-width="2" fill="none"/></svg>Nibh euismod tincidunt ut laoreet dolore magna</li>
    <li style="top:64px"><svg width="10" height="8" viewBox="0 0 10 8"><path d="M1 4l3 3 5-6" stroke="#1a9fe0" stroke-width="2" fill="none"/></svg>Aliquam erat volutpat. Ut wisi enim ad minim veniam</li>
    <li style="top:96px"><svg width="10" height="8" viewBox="0 0 10 8"><path d="M1 4l3 3 5-6" stroke="#1a9fe0" stroke-width="2" fill="none"/></svg>Quis nostrud exerci tation ullamcorper suscipit lobortis</li>
  </ul>
  <div class="dash" style="left:631px;top:0">
    <div class="bar"></div>
    <div class="card profile"><div class="avatar"></div><div class="handle">@username</div><div class="line" style="left:12px;top:90px;width:81px"></div><div class="line" style="left:18px;top:96px;width:69px"></div><div class="line" style="left:22px;top:106px;width:60px"></div></div>
    <div class="card feed"><div class="hero"></div><div class="line" style="left:6px;top:88px;width:90px"></div><div class="line" style="left:6px;top:95px;width:80px"></div><div class="line" style="left:6px;top:102px;width:86px"></div><div class="line" style="left:6px;top:140px;width:90px"></div><div class="line" style="left:6px;top:147px;width:78px"></div><div class="line" style="left:6px;top:180px;width:88px"></div><div class="line" style="left:6px;top:187px;width:72px"></div><div class="foot"></div></div>
    <div class="card contacts"><div class="label">Contact</div><div class="pip" style="left:6px;top:20px;background:#f29b42"></div><div class="pip" style="left:6px;top:44px;background:#9b5cc6"></div><div class="pip" style="left:6px;top:68px;background:#6b86c9"></div><div class="pip" style="left:6px;top:92px;background:#e0645a"></div><div class="pip" style="left:6px;top:116px;background:#8cc4a8"></div></div>
    <div class="card calendar"><div class="label">Calendar</div><div class="line" style="left:8px;top:22px;width:88px"></div><div class="line" style="left:8px;top:38px;width:88px"></div><div class="line" style="left:8px;top:48px;width:88px"></div><div class="line" style="left:8px;top:58px;width:88px"></div><div class="line" style="left:8px;top:68px;width:88px"></div><div class="line" style="left:8px;top:78px;width:20px"></div></div>
  </div>
</section>

<section class="feature" style="top:1762px">
  <div class="ring" style="left:-30px;top:-128px;width:480px;height:480px"></div>
  <div class="dash" style="left:176px;top:0">
    <div class="bar"></div>
    <div class="card profile"><div class="avatar"></div><div class="handle">@username</div><div class="line" style="left:12px;top:90px;width:81px"></div><div class="line" style="left:18px;top:96px;width:69px"></div><div class="line" style="left:22px;top:106px;width:60px"></div></div>
    <div class="card feed"><div class="hero"></div><div class="line" style="left:6px;top:88px;width:90px"></div><div class="line" style="left:6px;top:95px;width:80px"></div><div class="line" style="left:6px;top:102px;width:86px"></div><div class="line" style="left:6px;top:140px;width:90px"></div><div class="line" style="left:6px;top:147px;width:78px"></div><div class="line" style="left:6px;top:180px;width:88px"></div><div class="line" style="left:6px;top:187px;width:72px"></div><div class="foot"></div></div>
    <div class="card contacts"><div class="label">Contact</div><div class="pip" style="left:6px;top:20px;background:#f29b42"></div><div class="pip" style="left:6px;top:44px;background:#9b5cc6"></div><div class="pip" style="left:6px;top:68px;background:#6b86c9"></div><div class="pip" style="left:6px;top:92px;background:#e0645a"></div><div class="pip" style="left:6px;top:116px;background:#8cc4a8"></div></div>
    <div class="card calendar"><div class="label">Calendar</div><div class="line" style="left:8px;top:22px;width:88px"></div><div class="line" style="left:8px;top:38px;width:88px"></div><div class="line" style="left:8px;top:48px;width:88px"></div><div class="line" style="left:8px;top:58px;width:88px"></div><div class="line" style="left:8px;top:68px;width:88px"></div><div class="line" style="left:8px;top:78px;width:20px"></div></div>
  </div>
  <h2 style="left:648px;top:18px">Cotetuer Adipiscing</h2>
  <p class="copy" style="left:649px;top:68px;width:400px">Lorem ipsum dolor sit amet, consectetuer adipiscing elit, sed diam nonummy nibh euismod tincidunt ut laoreet dolore magna aliquam erat volutpat. Ut wisi enim ad minim veniam</p>
  <ul class="checks" style="left:649px;top:146px">
    <li style="top:0"><svg width="10" height="8" viewBox="0 0 10 8"><path d="M1 4l3 3 5-6" stroke="#1a9fe0" stroke-width="2" fill="none"/></svg>Consectetuer adipiscing elit sed diam nonummy</li>
    <li style="top:32px"><svg width="10" height="8" viewBox="0 0 10 8"><path d="M1 4l3 3 5-6" stroke="#1a9fe0" stroke-width="2" fill="none"/></svg>Nibh euismod tincidunt ut laoreet dolore magna</li>
    <li style="top:64px"><svg width="10" height="8" viewBox="0 0 10 8"><path d="M1 4l3 3 5-6" stroke="#1a9fe0" stroke-width="2" fill="none"/></svg>Aliquam erat volutpat. Ut wisi enim ad minim veniam</li>
    <li style="top:96px"><svg width="10" height="8" viewBox="0 0 10 8"><path d="M1 4l3 3 5-6" stroke="#1a9fe0" stroke-width="2" fill="none"/></svg>Quis nostrud exerci tation ullamcorper suscipit lobortis</li>
  </ul>
</section>

<section class="feature" style="top:2249px">
  <div class="ring" style="left:740px;top:-100px;width:480px;height:480px"></div>
  <h2 style="left:137px;top:18px">Client Calibration</h2>
  <p class="copy" style="left:138px;top:68px;width:400px">Lorem ipsum dolor sit amet, consectetuer adipiscing elit, sed diam nonummy nibh euismod tincidunt ut laoreet dolore magna aliquam erat volutpat. Ut wisi enim ad minim veniam</p>
  <ul class="checks" style="left:138px;top:146px">
    <li style="top:0"><svg width="10" height="8" viewBox="0 0 10 8"><path d="M1 4l3 3 5-6" stroke="#1a9fe0" stroke-width="2" fill="none"/></svg>Consectetuer adipiscing elit sed diam nonummy</li>
    <li style="top:32px"><svg width="10" height="8" viewBox="0 0 10 8"><path d="M1 4l3 3 5-6" stroke="#1a9fe0" stroke-width="2" fill="none"/></svg>Nibh euismod tincidunt ut laoreet dolore magna</li>
    <li style="top:64px"><svg width="10" height="8" viewBox="0 0 10 8"><path d="M1 4l3 3 5-6" stroke="#1a9fe0" stroke-width="2" fill="none"/></svg>Aliquam erat volutpat. Ut wisi enim ad minim veniam</li>
    <li style="top:96px"><svg width="10" height="8" viewBox="0 0 10 8"><path d="M1 4l3 3 5-6" stroke="#1a9fe0" stroke-width="2" fill="none"/></svg>Quis nostrud exerci tation ullamcorper suscipit lobortis</li>
  </ul>
  <div class="dash" style="left:631px;top:0">
    <div class="bar"></div>
    <div class="card profile"><div class="avatar"></div><div class="handle">@username</div><div class="line" style="left:12px;top:90px;width:81px"></div><div class="line" style="left:18px;top:96px;width:69px"></div><div class="line" style="left:22px;top:106px;width:60px"></div></div>
    <div class="card feed"><div class="hero"></div><div class="line" style="left:6px;top:88px;width:90px"></div><div class="line" style="left:6px;top:95px;width:80px"></div><div class="line" style="left:6px;top:102px;width:86px"></div><div class="line" style="left:6px;top:140px;width:90px"></div><div class="line" style="left:6px;top:147px;width:78px"></div><div class="line" style="left:6px;top:180px;width:88px"></div><div class="line" style="left:6px;top:187px;width:72px"></div><div class="foot"></div></div>
    <div class="card contacts"><div class="label">Contact</div><div class="pip" style="left:6px;top:20px;background:#f29b42"></div><div class="pip" style="left:6px;top:44px;background:#9b5cc6"></div><div class="pip" style="left:6px;top:68px;background:#6b86c9"></div><div class="pip" style="left:6px;top:92px;background:#e0645a"></div><div class="pip" style="left:6px;top:116px;background:#8cc4a8"></div></div>
    <div class="card calendar"><div class="label">Calendar</div><div class="line" style="left:8px;top:22px;width:88px"></div><div class="line" style="left:8px;top:38px;width:88px"></div><div class="line" style="left:8px;top:48px;width:88px"></div><div class="line" style="left:8px;top:58px;width:88px"></div><div class="line" style="left:8px;top:68px;width:88px"></div><div class="line" style="left:8px;top:78px;width:20px"></div></div>
  </div>
</section>

<section class="feature" style="top:2736px">
  <div class="ring" style="left:-30px;top:-128px;width:480px;height:480px"></div>
  <div class="dash" style="left:176px;top:0">
    <div class="bar"></div>
    <div class="card profile"><div class="avatar"></div><div class="handle">@username</div><div class="line" style="left:12px;top:90px;width:81px"></div><div class="line" style="left:18px;top:96px;width:69px"></div><div class="line" style="left:22px;top:106px;width:60px"></div></div>
    <div class="card feed"><div class="hero"></div><div class="line" style="left:6px;top:88px;width:90px"></div><div class="line" style="left:6px;top:95px;width:80px"></div><div class="line" style="left:6px;top:102px;width:86px"></div><div class="line" style="left:6px;top:140px;width:90px"></div><div class="line" style="left:6px;top:147px;width:78px"></div><div class="line" style="left:6px;top:180px;width:88px"></div><div class="line" style="left:6px;top:187px;width:72px"></div><div class="foot"></div></div>
    <div class="card contacts"><div class="label">Contact</div><div class="pip" style="left:6px;top:20px;background:#f29b42"></div><div class="pip" style="left:6px;top:44px;background:#9b5cc6"></div><div class="pip" style="left:6px;top:68px;background:#6b86c9"></div><div class="pip" style="left:6px;top:92px;background:#e0645a"></div><div class="pip" style="left:6px;top:116px;background:#8cc4a8"></div></div>
    <div class="card calendar"><div class="label">Calendar</div><div class="line" style="left:8px;top:22px;width:88px"></div><div class="line" style="left:8px;top:38px;width:88px"></div><div class="line" style="left:8px;top:48px;width:88px"></div><div class="line" style="left:8px;top:58px;width:88px"></div><div class="line" style="left:8px;top:68px;width:88px"></div><div class="line" style="left:8px;top:78px;width:20px"></div></div>
  </div>
  <h2 style="left:648px;top:18px">Cotetuer Adipiscing</h2>
  <p class="copy" style="left:649px;top:68px;width:400px">Lorem ipsum dolor sit amet, consectetuer adipiscing elit, sed diam nonummy nibh euismod tincidunt ut laoreet dolore magna aliquam erat volutpat. Ut wisi enim ad minim veniam</p>
  <ul class="checks" style="left:649px;top:146px">
    <li style="top:0"><svg width="10" height="8" viewBox="0 0 10 8"><path d="M1 4l3 3 5-6" stroke="#1a9fe0" stroke-width="2" fill="none"/></svg>Consectetuer adipiscing elit sed diam nonummy</li>
    <li style="top:32px"><svg width="10" height="8" viewBox="0 0 10 8"><path d="M1 4l3 3 5-6" stroke="#1a9fe0" stroke-width="2" fill="none"/></svg>Nibh euismod tincidunt ut laoreet dolore magna</li>
    <li style="top:64px"><svg width="10" height="8" viewBox="0 0 10 8"><path d="M1 4l3 3 5-6" stroke="#1a9fe0" stroke-width="2" fill="none"/></svg>Aliquam erat volutpat. Ut wisi enim ad minim veniam</li>
    <li style="top:96px"><svg width="10" height="8" viewBox="0 0 10 8"><path d="M1 4l3 3 5-6" stroke="#1a9fe0" stroke-width="2" fill="none"/></svg>Quis nostrud exerci tation ullamcorper suscipit lobortis</li>
  </ul>
</section>

<!-- footer -->
<footer class="abs footer">
  <h3 style="left:138px;top:58px">Quick Links</h3>
  <span class="link" style="left:139px;top:93px">Home</span>
  <span class="link" style="left:139px;top:113px">Services</span>
  <span class="link" style="left:139px;top:134px">System Details</span>
  <span class="link" style="left:139px;top:154px">Pricing</span>
  <span class="link" style="left:293px;top:93px">Team</span>
  <span class="link" style="left:293px;top:113px">Blog</span>
  <span class="link" style="left:293px;top:134px">Contact Us</span>
  <span class="link" style="left:293px;top:154px">Login</span>

  <h3 style="left:460px;top:58px">Contact Us</h3>
  <svg class="abs" style="left:462px;top:96px" width="11" height="15" viewBox="0 0 12 16"><path d="M6 0a6 6 0 0 0-6 6c0 4.5 6 10 6 10s6-5.5 6-10a6 6 0 0 0-6-6zm0 8.5A2.5 2.5 0 1 1 6 3.5a2.5 2.5 0 0 1 0 5z" fill="#fff"/></svg>
  <div class="info" style="left:479px;top:90px">4410 Harbor Lane<br>Pasadena, CA 91101</div>
  <svg class="abs" style="left:660px;top:96px" width="13" height="13" viewBox="0 0 24 24" fill="#fff"><path d="M6.6 10.8a15.1 15.1 0 0 0 6.6 6.6l2.2-2.2c.3-.3.7-.4 1-.2 1.1.4 2.3.6 3.6.6.6 0 1 .4 1 1V20c0 .6-.4 1-1 1A17 17 0 0 1 3 4c0-.6.4-1 1-1h3.5c.6 0 1 .4 1 1 0 1.3.2 2.5.6 3.6.1.3 0 .7-.2 1z"/></svg>
  <div class="info" style="left:681px;top:90px">800-555-0142</div>
  <svg class="abs" style="left:660px;top:132px" width="14" height="11" viewBox="0 0 14 11"><rect width="14" height="11" rx="1" fill="#fff"/><path d="M1 1l6 5 6-5" stroke="#0b2550" stroke-width="1.3" fill="none"/></svg>
  <div class="info" style="left:681px;top:125px">hello@voxmetric.com</div>

  <div class="mark"><span class="dot"></span>VoxMetric</div>
  <div class="rule"></div>
  <div class="copyright">Copyright © 2019 VOXMETRIC. All Rights Reserved.</div>
</footer>

</body>
</html>
```